Event flyer for Sunday night Youth Group

Need a 4 x 6 or 5 x 7 flyer for a new youth group starting on April 14. The youth group is for students in middle school and high school so it needs to look fun and cool, but not childish. I prefer it not to include pictures of people unless it's so obscure you can't really see their faces. I've uploaded some pictures of flyers I like. I've also attached a couple versions of our logo to use on the flyer.
Information the flyer needs to include:
Youth Group
Sundays, 6-8pm (beginning April 14)
Location: Marlowe's - 4219 Quarry Fern Ave N, Keizer, 97318
There will be dinner, games, friends, and a message.
Target Market(s)
Youth ages 13-18
Industry/Entity Type
Church
Font styles to use
Colors
Designer to choose colors to be used in the design.
Look and feel

```html
<!DOCTYPE html>
<html lang="en">
<head>
<meta charset="utf-8">
<title>Youth Group Flyer – Harborline Fellowship</title>
<link rel="stylesheet" href="https://fonts.googleapis.com/css2?family=Anton&family=Montserrat:wght@400;500;700;800&family=Yellowtail&display=swap">
<style>
  :root {
    --stage: #333333;
    --ink: #1d1d1d;
    --slate: #264552;
    --red: #e3321b;
    --orange: #ff5a1f;
    --amber: #ffa800;
    --gold-line: #d9a441;
    --teal: #12a6c2;
    --blue: #2f6fd6;
    --purple: #7a2cf0;
    --paper: #ffffff;
  }
  * { box-sizing: border-box; margin: 0; padding: 0; }
  html, body { width: 1200px; height: 2259px; overflow: hidden; }
  body { background: var(--stage); font-family: "Montserrat", sans-serif; color: var(--ink); }

  .flyer {
    position: absolute; left: 100px; top: 448px;
    width: 1000px; height: 1362px; overflow: hidden;
  }
  .flyer__wash {
    position: absolute; inset: 0;
    background:
      radial-gradient(ellipse 60% 40% at 8% 4%, #f3b2ef 0%, rgba(243,178,239,0) 70%),
      radial-gradient(ellipse 55% 35% at 95% 98%, #ffb24a 0%, rgba(255,178,74,0) 75%),
      radial-gradient(ellipse 50% 40% at 90% 55%, #ece6d6 0%, rgba(236,230,214,0) 70%),
      linear-gradient(160deg, #fbe3f4 0%, #fcefe3 30%, #fbf0bf 60%, #fde58f 85%, #ffc56a 100%);
  }

  .brand {
    position: absolute; top: 100px; left: 0; width: 1000px;
    display: flex; justify-content: center; align-items: center; gap: 22px;
  }
  .brand__mark { width: 58px; height: 58px; background: var(--slate); }
  .brand__name {
    font-weight: 500; font-size: 44px; letter-spacing: 3px;
    color: var(--slate); line-height: 1;
  }

  .rings { position: absolute; left: 0; top: 0; }

  .title { position: absolute; left: 0; width: 1000px; text-align: center; }
  .title--script {
    top: 230px; font-family: "Yellowtail", cursive; font-size: 250px;
    line-height: 1; color: var(--red); transform: rotate(-6deg); left: 10px;
    text-shadow: 3px 3px 0 rgba(255,255,255,.7); z-index: 2;
  }
  .title--block {
    top: 470px; font-family: "Anton", sans-serif; font-size: 200px;
    line-height: 1; color: var(--slate); letter-spacing: 2px;
  }

  .schedule { position: absolute; left: 0; width: 1000px; top: 668px; text-align: center; }
  .schedule__day {
    font-weight: 800; font-size: 52px; color: var(--orange); line-height: 1; letter-spacing: 1px;
  }
  .schedule__rule { width: 440px; height: 2px; background: var(--gold-line); margin: 10px auto 12px; }
  .schedule__time { font-weight: 700; font-size: 50px; line-height: 1; color: var(--ink); }
  .schedule__start { font-weight: 400; font-size: 32px; letter-spacing: 4px; line-height: 1; }

  .location {
    position: absolute; top: 1055px; left: 57px; width: 887px; height: 50px;
    display: flex; border: 2px solid var(--red); border-radius: 5px; overflow: hidden;
  }
  .location__label {
    width: 236px; background: rgba(255,255,255,.55);
    font-weight: 700; font-size: 30px; letter-spacing: 5px; color: var(--ink);
    display: flex; align-items: center; justify-content: center;
  }
  .location__address {
    flex: 1; background: var(--red); color: var(--paper);
    font-size: 22px; font-weight: 400;
    display: flex; align-items: center; justify-content: center;
  }
  .location__address strong { font-weight: 700; margin-right: 6px; }

  .extras__lead {
    position: absolute; top: 1138px; left: 0; width: 1000px; text-align: center;
    font-size: 32px; font-weight: 500; letter-spacing: 8px; line-height: 1;
  }
  .extras {
    position: absolute; top: 1189px; left: 57px; width: 887px;
    display: flex; justify-content: space-between; list-style: none;
  }
  .extras__item {
    width: 204px; height: 40px; display: flex; align-items: center; justify-content: center;
    font-weight: 800; font-size: 27px; letter-spacing: 3px; line-height: 1;
  }
  .extras__item--amber { background: var(--amber); color: var(--ink); }
  .extras__item--orange { background: var(--orange); color: var(--paper); }

  .website {
    position: absolute; top: 1262px; left: 0; width: 1000px; text-align: center;
    font-size: 26px; letter-spacing: 5px; line-height: 1;
  }
  .website strong { font-weight: 700; }
</style>
</head>
<body>
  <main class="flyer">
    <div class="flyer__wash" role="img" aria-label="Soft pink, yellow and orange watercolor wash with a faint blurred crowd of raised hands"></div>

    <header class="brand">
      <span class="brand__mark"></span>
      <span class="brand__name">HARBORLINE FELLOWSHIP</span>
    </header>

    <svg class="rings" width="1000" height="1362" viewBox="0 0 1000 1362" aria-hidden="true">
      <circle cx="500" cy="588" r="400" fill="none" stroke="#ff6a1a" stroke-width="3"/>
      <circle cx="514" cy="596" r="388" fill="none" stroke="#12a6c2" stroke-width="3"/>
      <circle cx="494" cy="600" r="392" fill="none" stroke="#2f6fd6" stroke-width="2"/>
      <circle cx="508" cy="580" r="380" fill="none" stroke="#ff5a1f" stroke-width="2"/>
      <path d="M196 704 A330 330 0 0 1 393 281" fill="none" stroke="#ffc21a" stroke-width="44"/>
      <path d="M393 281 A330 330 0 0 1 671 877" fill="none" stroke="#12a6c2" stroke-width="46"/>
      <path d="M825 707 A340 340 0 0 1 506 931" fill="none" stroke="#7a2cf0" stroke-width="18"/>
      <path d="M671 877 A330 330 0 0 1 181 534" fill="none" stroke="#ff5a1f" stroke-width="44"/>
      <circle cx="506" cy="591" r="312" fill="#ffffff"/>
    </svg>

    <h1>
      <span class="title title--script">Youth</span>
      <span class="title title--block">GROUP</span>
    </h1>

    <section class="schedule">
      <p class="schedule__day">EVERY SUNDAY</p>
      <div class="schedule__rule"></div>
      <p class="schedule__time">6:00PM–8:00PM</p>
      <div class="schedule__rule"></div>
      <p class="schedule__start">(BEGINNING APRIL 14)</p>
    </section>

    <div class="location">
      <span class="location__label">LOCATION</span>
      <span class="location__address"><strong>MARLOWE'S –</strong> 4219 QUARRY FERN AVE N, KEIZER, 97318</span>
    </div>

    <p class="extras__lead">THERE WILL BE</p>
    <ul class="extras">
      <li class="extras__item extras__item--amber">DINNER</li>
      <li class="extras__item extras__item--orange">GAMES</li>
      <li class="extras__item extras__item--amber">FRIENDS</li>
      <li class="extras__item extras__item--orange">A MESSAGE</li>
    </ul>

    <p class="website">www.<strong>harborline-fellowship</strong>.church</p>
  </main>
</body>
</html>
```